QuillVane needs a dashboard page designed

Redesign the dashboard shown in the provided images.

There are two images:
- dashboard.png
- dashboard-expanded.png

NOTE: The vocabulary navigation on the left will be a very long list of words 100s, so keep that in mind when you're designing both the vocab navigation and the expanded vocab popup.

In the dashboard.png picture, there needs to be a progress chart showing the word progress like the following: review 1(show it as completed) -> review 2(show the user they are here) -> review 3(unvisited) -> review 4(unvisited)

The do-not-design-this-page.png image is for your reference only. It is not to be designed. Use it to understand the overall look and feel of the website to help you create the best dashboard page possible.
Updates

Need extra days to review

Industry/Entity Type

Education English learning

Number of Pages Required

1 page

Requirements
Must have
• The main navigation and main header cannot change between pages. See the do-not-design page for the main navigateion and header.
Should not have
• Do not add a person profile. We will not have images of our users. Keep the icons in the main navigation as they are.

```html
<!DOCTYPE html>
<html lang="en">
<head>
<meta charset="utf-8">
<title>QuillVane Tutor – Vocabulary Dashboard</title>
<link href="https://fonts.googleapis.com/css2?family=Roboto:wght@400;500;700&display=swap" rel="stylesheet">
<style>
:root{
  --blue:#1c50a0;
  --blue-dark:#173f80;
  --blue-pale:#dfe8f7;
  --header:#bcd3f1;
  --screen:#f3f6fb;
  --panel:#ffffff;
  --ink:#222831;
  --text:#505660;
  --line:#d9dde3;
  --red:#e53935;
  --note-bg:#edf3fc;
  --note-border:#cfdbee;
  --star:#f5b120;
  --magenta:#a8359a;
}
*{box-sizing:border-box;margin:0;padding:0}
html,body{width:877px;height:1200px;overflow:hidden}
body{font-family:'Roboto',sans-serif;background:linear-gradient(180deg,#5f5f5f 0%,#7a7a7a 45%,#6d6d6d 100%);position:relative;color:var(--ink)}
.screen{position:absolute;left:47px;width:783px;height:538px;background:var(--screen);overflow:hidden;box-shadow:0 6px 24px rgba(0,0,0,.35)}
.screen--main{top:52px}
.screen--popup{top:609px}
.abs{position:absolute}
.sidebar{left:8px;top:10px;width:57px;height:519px;background:var(--blue);border-radius:7px;color:#fff}
.nav-item{position:absolute;left:0;width:57px;text-align:center;font-size:8.5px;line-height:11px}
.nav-item svg{display:block;margin:0 auto 4px;width:13px;height:13px;fill:#fff}
.nav-rule{position:absolute;left:7px;width:43px;height:1px;background:rgba(255,255,255,.25)}
.topbar{left:71px;top:14px;width:703px;height:39px;background:var(--header);border-radius:6px}
.topbar-title{position:absolute;left:0;right:0;top:11px;text-align:center;font-size:11.7px;font-weight:500;color:#1e2430}
.topbar-title .caret{display:inline-block;margin-left:10px;border:3px solid transparent;border-top:3.5px solid #1e2430;vertical-align:middle;margin-top:2px}
.tool{position:absolute;top:10px;width:20px;height:20px;border-radius:50%;background:#fff;display:flex;align-items:center;justify-content:center}
.tool svg{width:9px;height:9px;fill:#1e2430}
.tool--user{background:var(--blue)}
.tool--user svg{fill:#fff}
.user-caret{position:absolute;top:19px;left:749px;border:2.5px solid transparent;border-top:3px solid #1e2430}
.panel{background:var(--panel);border-radius:7px;box-shadow:0 1px 4px rgba(0,0,0,.08)}
.vocab{left:71px;top:58px;width:159px;height:472px}
.select{position:absolute;width:48px;height:22px;border:1px solid #b9bec6;border-radius:3px;font-size:9.5px;padding:5px 0 0 9px;color:var(--ink);background:#fff}
.select::after{content:"";position:absolute;right:9px;top:9px;border:3px solid transparent;border-top:3.5px solid var(--ink)}
.expand{position:absolute;left:82px;top:22px;font-size:8.5px;color:var(--ink)}
.expand-icon{position:absolute;left:134px;top:23px;width:9px;height:9px}
.rule{position:absolute;height:1px;background:var(--line)}
.group-head{position:absolute;font-size:8.5px;font-weight:500;color:var(--ink);white-space:nowrap}
.group-icon{position:absolute;width:9px;height:9px;fill:var(--blue)}
.help{position:absolute;width:7px;height:7px;border:0.8px solid #555;border-radius:50%;font-size:5px;text-align:center;line-height:5.5px;color:#555}
.word{position:absolute;font-size:8.5px;color:var(--ink);white-space:nowrap}
.word--active{color:var(--red)}
.content{left:237px;top:58px;width:537px;height:472px}
.step{position:absolute;top:26px;width:45px;height:45px;border-radius:50%;display:flex;align-items:center;justify-content:center;text-align:center;font-size:7.8px;font-weight:700;line-height:10px}
.step--done,.step--current{background:var(--blue);color:#fff}
.step--todo{background:var(--blue-pale);color:#2a3340}
.track{position:absolute;top:47px;height:2px}
.track--done{left:76px;width:100px;background:var(--blue)}
.track--todo{left:218px;width:250px;background:var(--blue-pale)}
.track-dot{position:absolute;left:220px;top:42px;width:11px;height:11px;border-radius:50%;background:var(--blue-pale)}
.track-dot::after{content:"";position:absolute;left:3px;top:3px;width:5px;height:5px;border-radius:50%;background:var(--blue)}
.word-title{position:absolute;left:31px;top:90px;font-size:16px;font-weight:500;color:#2a2f36}
.star{position:absolute;left:80px;top:91px;width:18px;height:18px;fill:var(--star)}
.cta{position:absolute;left:285px;top:87px;width:220px;height:26px;border-radius:13px;background:var(--blue);color:#fff;font-size:8.6px;font-weight:700;text-align:center;line-height:26px;letter-spacing:.1px}
.note{position:absolute;left:12px;top:128px;width:513px;height:72px;background:var(--note-bg);border:1px solid var(--note-border);border-radius:4px;padding:8px 18px 8px 19px;font-size:8.45px;line-height:13px;color:var(--text)}
.chart{position:absolute;left:12px;top:208px;width:513px;height:150px;border:1px solid var(--line);border-radius:4px;background:#fff}
.chart svg{display:block}
.analysis-title{position:absolute;left:25px;top:377px;font-size:13px;font-weight:500;color:#2a2f36}
.analysis-text{position:absolute;left:25px;top:403px;width:492px;font-size:8.45px;line-height:13px;color:var(--text)}
.dim{position:absolute;inset:0;background:rgba(10,18,35,.62)}
.modal{left:88px;top:101px;width:608px;height:270px;background:#fff;border-radius:8px;box-shadow:0 6px 20px rgba(0,0,0,.3)}
.close{position:absolute;left:657px;top:95px;width:40px;height:40px;border-radius:50%;background:var(--blue);display:flex;align-items:center;justify-content:center}
.close svg{width:12px;height:12px;stroke:#fff;stroke-width:3}
.word-row{position:absolute;left:58px;top:164px;display:flex;gap:20.5px;font-size:8.5px;color:var(--ink)}
</style>
</head>
<body>
<svg width="0" height="0" style="position:absolute" aria-hidden="true">
  <symbol id="i-home" viewBox="0 0 16 16"><path d="M8 1.5 0.5 8h2.2v6.5h4v-4h2.6v4h4V8h2.2z"/></symbol>
  <symbol id="i-flag" viewBox="0 0 16 16"><path d="M2 1h1.6v14H2zM4.2 2.2c2.6-1.3 4.6 1 7.6 0v7c-3 1-5-1.3-7.6 0z"/></symbol>
  <symbol id="i-building" viewBox="0 0 16 16"><path d="M3 1h10v14H9.5v-3h-3v3H3zM5 3v2h2V3zm4 0v2h2V3zM5 7v2h2V7zm4 0v2h2V7z" fill-rule="evenodd"/></symbol>
  <symbol id="i-clock" viewBox="0 0 16 16"><path d="M8 1a7 7 0 1 0 0 14A7 7 0 0 0 8 1zm.8 3v4.3l2.7 1.6-.8 1.3L7.2 9.1V4z"/></symbol>
  <symbol id="i-db" viewBox="0 0 16 16"><ellipse cx="8" cy="3.2" rx="6" ry="2.2"/><path d="M2 5.2c0 1.2 2.7 2.2 6 2.2s6-1 6-2.2v2.6c0 1.2-2.7 2.2-6 2.2S2 9 2 7.8zm0 4.4c0 1.2 2.7 2.2 6 2.2s6-1 6-2.2v2.6c0 1.2-2.7 2.2-6 2.2s-6-1-6-2.2z"/></symbol>
  <symbol id="i-lock" viewBox="0 0 16 16"><path d="M4.5 7V5a3.5 3.5 0 0 1 7 0v2H13v8H3V7zm1.8 0h3.4V5a1.7 1.7 0 0 0-3.4 0z"/></symbol>
  <symbol id="i-gear" viewBox="0 0 16 16"><path d="M6.8 0h2.4l.4 2.2 1.5.7 1.9-1.3 1.7 1.7-1.3 1.9.7 1.5 2.2.4v2.4l-2.2.4-.7 1.5 1.3 1.9-1.7 1.7-1.9-1.3-1.5.7-.4 2.2H6.8l-.4-2.2-1.5-.7-1.9 1.3-1.7-1.7 1.3-1.9-.7-1.5L0 9.2V6.8l2.2-.4.7-1.5-1.3-1.9 1.7-1.7 1.9 1.3 1.5-.7zM8 5.4a2.6 2.6 0 1 0 0 5.2 2.6 2.6 0 0 0 0-5.2z" fill-rule="evenodd"/></symbol>
  <symbol id="i-check" viewBox="0 0 16 16"><path d="M1.5 8.5 3.6 6.4 6.3 9.1 12.4 3l2.1 2.1-8.2 8.2z"/></symbol>
  <symbol id="i-user" viewBox="0 0 16 16"><circle cx="8" cy="4.5" r="3.5"/><path d="M1.5 15c0-3.6 2.9-6 6.5-6s6.5 2.4 6.5 6z"/></symbol>
  <symbol id="i-expand" viewBox="0 0 16 16"><path d="M1 1h5v2H3v3H1zM10 1h5v5h-2V3h-3zM1 10h2v3h3v2H1zM13 10h2v5h-5v-2h3z" fill="#222"/></symbol>
  <symbol id="i-star" viewBox="0 0 16 16"><path d="M8 .8l2.2 4.7 5.1.6-3.8 3.5 1 5.1L8 12.2l-4.5 2.5 1-5.1L.7 6.1l5.1-.6z"/></symbol>
</svg>

<!-- Dashboard -->
<section class="screen screen--main">
  <nav class="abs sidebar">
    <div class="nav-item" style="top:18px"><svg><use href="#i-home"/></svg>QuillVane<br>Tutor</div>
    <div class="nav-rule" style="top:71px"></div>
    <div class="nav-item" style="top:86px"><svg><use href="#i-flag"/></svg>Daily<br>English</div>
    <div class="nav-rule" style="top:139px"></div>
    <div class="nav-item" style="top:153px"><svg><use href="#i-building"/></svg>Business</div>
    <div class="nav-rule" style="top:197px"></div>
  </nav>
  <header class="abs topbar">
    <div class="topbar-title">QuillVane Tutor<span class="caret"></span></div>
  </header>
  <div class="tool" style="left:676px;top:24px"><svg><use href="#i-gear"/></svg></div>
  <div class="tool" style="left:700px;top:24px"><svg><use href="#i-check"/></svg></div>
  <div class="tool tool--user" style="left:725px;top:24px"><svg><use href="#i-user"/></svg></div>
  <div class="user-caret" style="top:32px"></div>

  <aside class="abs panel vocab">
    <div class="select" style="left:17px;top:17px">All</div>
    <div class="expand">Expand</div>
    <svg class="expand-icon"><use href="#i-expand"/></svg>
    <div class="rule" style="left:7px;width:146px;top:52px"></div>
    <svg class="group-icon" style="left:21px;top:75px"><use href="#i-clock"/></svg>
    <div class="group-head" style="left:44px;top:74px">Short-Term Memory</div>
    <div class="help" style="left:130px;top:76px">?</div>
    <div class="word word--active" style="left:44px;top:95px">Grab</div>
    <div class="rule" style="left:7px;width:146px;top:120px"></div>
    <svg class="group-icon" style="left:21px;top:133px"><use href="#i-db"/></svg>
    <div class="group-head" style="left:44px;top:131px">Working Memory</div>
    <div class="help" style="left:130px;top:133px">?</div>
    <div class="word" style="left:44px;top:153px">Cool Down</div>
    <div class="word" style="left:44px;top:174px">Crave</div>
    <div class="word" style="left:44px;top:196px">Go For</div>
    <div class="word" style="left:44px;top:217px">Go-To</div>
    <div class="word" style="left:44px;top:238px">In The Mood For</div>
    <div class="word" style="left:44px;top:260px">Sip</div>
    <div class="word" style="left:44px;top:281px">Soothing</div>
    <div class="word" style="left:44px;top:303px">Stick With</div>
    <div class="word" style="left:44px;top:324px">Throw In/Throw On</div>
    <div class="rule" style="left:7px;width:146px;top:350px"></div>
    <svg class="group-icon" style="left:21px;top:368px"><use href="#i-lock"/></svg>
    <div class="group-head" style="left:44px;top:367px">Long-Term Memory</div>
    <div class="help" style="left:130px;top:369px">?</div>
    <div class="word" style="left:44px;top:388px">Give It A Try</div>
  </aside>

  <main class="abs panel content">
    <div class="track track--done"></div>
    <div class="track track--todo"></div>
    <div class="track-dot"></div>
    <div class="step step--done" style="left:32px">Review<br>01</div>
    <div class="step step--current" style="left:174px">Review<br>02</div>
    <div class="step step--todo" style="left:317px">Review<br>03</div>
    <div class="step step--todo" style="left:460px">Review<br>04</div>
    <h1 class="word-title">Grab</h1>
    <svg class="star"><use href="#i-star"/></svg>
    <div class="cta">START VOCABULARY REVIEW EXERCISE 3</div>
    <p class="note">The word "grab" is most commonly used as a verb, meaning to take something quickly or suddenly. Imagine you're running late for school. You don't have time for breakfast, so you quickly grab an apple from the kitchen and rush out the door. As you reach the bus stop, your friend waves and says, "Hey! Let's grab a coffee after class. Later, when you sit down, your phone starts ringing. You grab it from your bag and answer.</p>
    <div class="chart">
      <svg width="511" height="148" viewBox="0 0 967 283" font-family="Roboto, sans-serif">
        <text x="484" y="33" text-anchor="middle" font-size="17" font-weight="700" fill="#222">Learning Curve Graph</text>
        <rect x="28" y="51" width="901" height="39" fill="#f6e7f5"/>
        <rect x="28" y="90" width="901" height="78" fill="#edf0f4"/>
        <rect x="28" y="168" width="901" height="22" fill="#eef8f2"/>
        <rect x="28" y="190" width="901" height="18" fill="#f3f3f3"/>
        <g font-size="9" font-weight="500" fill="#222">
          <text x="38" y="73">Long Term Memory</text>
          <text x="38" y="122">Working Memory</text>
          <text x="33" y="168">Short term</text>
          <text x="33" y="179">Memory</text>
          <text x="33" y="201">Forgotten Memory</text>
        </g>
        <rect x="111" y="175" width="14" height="33" fill="var(--magenta)"/>
        <rect x="200" y="97" width="15" height="111" fill="var(--magenta)"/>
        <path d="M133 170 C160 174 180 184 198 202" fill="none" stroke="#777" stroke-dasharray="1.5 2.5"/>
        <path d="M216 92 C260 96 290 98 310 110 C340 128 365 160 386 207" fill="none" stroke="#777" stroke-dasharray="1.5 2.5"/>
        <rect x="85" y="159" width="47" height="15" fill="#fff" stroke="var(--magenta)"/>
        <text x="108" y="170" text-anchor="middle" font-size="8.5" fill="var(--magenta)">May 18</text>
        <rect x="167" y="81" width="47" height="16" fill="#fff" stroke="var(--magenta)"/>
        <text x="190" y="92" text-anchor="middle" font-size="8.5" fill="var(--magenta)">May 19</text>
        <line x1="28" y1="208" x2="929" y2="208" stroke="#555"/>
        <g stroke="#555">
          <line x1="41" y1="208" x2="41" y2="214"/><line x1="86" y1="208" x2="86" y2="214"/><line x1="131" y1="208" x2="131" y2="214"/><line x1="176" y1="208" x2="176" y2="214"/><line x1="221" y1="208" x2="221" y2="214"/><line x1="266" y1="208" x2="266" y2="214"/><line x1="310" y1="208" x2="310" y2="214"/><line x1="355" y1="208" x2="355" y2="214"/><line x1="400" y1="208" x2="400" y2="214"/><line x1="445" y1="208" x2="445" y2="214"/><line x1="490" y1="208" x2="490" y2="214"/><line x1="535" y1="208" x2="535" y2="214"/><line x1="580" y1="208" x2="580" y2="214"/><line x1="625" y1="208" x2="625" y2="214"/><line x1="669" y1="208" x2="669" y2="214"/><line x1="714" y1="208" x2="714" y2="214"/><line x1="759" y1="208" x2="759" y2="214"/><line x1="804" y1="208" x2="804" y2="214"/><line x1="849" y1="208" x2="849" y2="214"/><line x1="894" y1="208" x2="894" y2="214"/>
        </g>
        <g font-size="8" fill="#333" text-anchor="middle">
          <text x="41" y="228">18 May</text><text x="86" y="228">12:00</text><text x="131" y="228">19 May</text><text x="176" y="228">12:00</text><text x="221" y="228">20 May</text><text x="266" y="228">12:00</text><text x="310" y="228">21 May</text><text x="355" y="228">12:00</text><text x="400" y="228">22 May</text><text x="445" y="228">12:00</text><text x="490" y="228">23 May</text><text x="535" y="228">12:00</text><text x="580" y="228">24 May</text><text x="625" y="228">12:00</text><text x="669" y="228">25 May</text><text x="714" y="228">12:00</text><text x="759" y="228">26 May</text><text x="804" y="228">12:00</text><text x="849" y="228">27 May</text><text x="894" y="228">12:00</text><text x="921" y="228">28</text>
        </g>
        <text x="483" y="260" text-anchor="middle" font-size="14" font-weight="700" fill="#222">Date Range</text>
      </svg>
    </div>
    <h2 class="analysis-title">QuillVane Tutor Learning Analysis</h2>
    <p class="analysis-text">Lorem ipsum dolor sit amet, consectetur adipiscing elit. Nam rutrum commodo enim id bibendum. Nunc dignissim risus erat, nec finibus nunc dictum eu. Aliquam sit amet euismod metus, quis malesuada erat. Sed at felis quis nulla feugiat cursus at at dolor. Maecenas pretium aliquet dapibus. Fusce et eleifend massa.</p>
  </main>
</section>

<!-- Dashboard with expanded vocabulary -->
<section class="screen screen--popup">
  <nav class="abs sidebar">
    <div class="nav-item" style="top:18px"><svg><use href="#i-home"/></svg>QuillVane<br>Tutor</div>
    <div class="nav-rule" style="top:71px"></div>
    <div class="nav-item" style="top:86px"><svg><use href="#i-flag"/></svg>Daily<br>English</div>
    <div class="nav-rule" style="top:139px"></div>
    <div class="nav-item" style="top:153px"><svg><use href="#i-building"/></svg>Business</div>
    <div class="nav-rule" style="top:197px"></div>
  </nav>
  <header class="abs topbar">
    <div class="topbar-title">QuillVane Tutor<span class="caret"></span></div>
  </header>
  <div class="tool" style="left:676px;top:24px"><svg><use href="#i-gear"/></svg></div>
  <div class="tool" style="left:700px;top:24px"><svg><use href="#i-check"/></svg></div>
  <div class="tool tool--user" style="left:725px;top:24px"><svg><use href="#i-user"/></svg></div>
  <div class="user-caret" style="top:32px"></div>

  <aside class="abs panel vocab">
    <div class="select" style="left:17px;top:17px">All</div>
    <div class="expand">Expand</div>
    <svg class="expand-icon"><use href="#i-expand"/></svg>
    <div class="rule" style="left:7px;width:146px;top:52px"></div>
    <div class="word" style="left:44px;top:324px">Throw In/Throw On</div>
    <div class="rule" style="left:7px;width:146px;top:350px"></div>
    <svg class="group-icon" style="left:21px;top:368px"><use href="#i-lock"/></svg>
    <div class="group-head" style="left:44px;top:367px">Long-Term Memory</div>
    <div class="help" style="left:130px;top:369px">?</div>
    <div class="word" style="left:44px;top:388px">Give It A Try</div>
  </aside>

  <main class="abs panel content">
    <div class="track track--done"></div>
    <div class="track track--todo"></div>
    <div class="step step--done" style="left:32px">Review<br>01</div>
    <div class="step step--current" style="left:174px">Review<br>02</div>
    <div class="step step--todo" style="left:317px">Review<br>03</div>
    <div class="step step--todo" style="left:460px">Review<br>04</div>
    <div class="cta">START VOCABULARY REVIEW EXERCISE 3</div>
    <p class="note">The word "grab" is most commonly used as a verb, meaning to take something quickly or suddenly. Imagine you're running late for school. You don't have time for breakfast, so you quickly grab an apple from the kitchen and rush out the door. As you reach the bus stop, your friend waves and says, "Hey! Let's grab a coffee after class. Later, when you sit down, your phone starts ringing.</p>
    <div class="chart">
      <svg width="511" height="148" viewBox="0 0 967 283" font-family="Roboto, sans-serif">
        <rect x="28" y="51" width="901" height="39" fill="#f6e7f5"/>
        <rect x="28" y="90" width="901" height="78" fill="#edf0f4"/>
        <rect x="111" y="175" width="14" height="33" fill="var(--magenta)"/>
        <rect x="200" y="97" width="15" height="111" fill="var(--magenta)"/>
        <line x1="28" y1="208" x2="929" y2="208" stroke="#555"/>
        <g font-size="8" fill="#333" text-anchor="middle">
          <text x="41" y="228">18 May</text><text x="86" y="228">12:00</text><text x="131" y="228">19 May</text><text x="176" y="228">12:00</text><text x="221" y="228">20 May</text><text x="266" y="228">12:00</text><text x="310" y="228">21 May</text><text x="355" y="228">12:00</text><text x="400" y="228">22 May</text><text x="445" y="228">12:00</text><text x="490" y="228">23 May</text><text x="535" y="228">12:00</text><text x="580" y="228">24 May</text><text x="625" y="228">12:00</text><text x="669" y="228">25 May</text><text x="714" y="228">12:00</text><text x="759" y="228">26 May</text><text x="804" y="228">12:00</text><text x="849" y="228">27 May</text><text x="894" y="228">12:00</text><text x="921" y="228">28</text>
        </g>
        <text x="483" y="260" text-anchor="middle" font-size="14" font-weight="700" fill="#222">Date Range</text>
      </svg>
    </div>
    <h2 class="analysis-title">QuillVane Tutor Learning Analysis</h2>
    <p class="analysis-text">Lorem ipsum dolor sit amet, consectetur adipiscing elit. Nam rutrum commodo enim id bibendum. Nunc dignissim risus erat, nec finibus nunc dictum eu. Aliquam sit amet euismod metus, quis malesuada erat. Sed at felis quis nulla feugiat cursus at at dolor. Maecenas pretium aliquet dapibus. Fusce et eleifend massa.</p>
  </main>

  <div class="dim"></div>

  <div class="abs modal" role="dialog" aria-label="All vocabulary">
    <div class="select" style="left:32px;top:20px">All</div>
    <div class="rule" style="left:22px;width:559px;top:56px"></div>
    <svg class="group-icon" style="left:36px;top:79px"><use href="#i-clock"/></svg>
    <div class="group-head" style="left:58px;top:78px">Short-Term Memory</div>
    <div class="help" style="left:145px;top:80px">?</div>
    <div class="word word--active" style="left:58px;top:99px">Grab</div>
    <div class="rule" style="left:22px;width:559px;top:124px"></div>
    <svg class="group-icon" style="left:36px;top:137px"><use href="#i-db"/></svg>
    <div class="group-head" style="left:58px;top:135px">Working Memory</div>
    <div class="help" style="left:145px;top:137px">?</div>
    <div class="word-row">
      <span>Cool Down</span><span>Crave</span><span>Go For</span><span>Go-To</span><span>In The Mood For</span><span>Sip</span><span>Soothing</span><span>Stick With</span><span>Throw In/Throw On</span>
    </div>
    <div class="rule" style="left:22px;width:559px;top:198px"></div>
    <svg class="group-icon" style="left:36px;top:215px"><use href="#i-lock"/></svg>
    <div class="group-head" style="left:58px;top:214px">Long-Term Memory</div>
    <div class="help" style="left:145px;top:216px">?</div>
    <div class="word" style="left:58px;top:235px">Give It A Try</div>
  </div>
  <div class="close"><svg viewBox="0 0 12 12"><path d="M2 2l8 8M10 2l-8 8"/></svg></div>
</section>
</body>
</html>
```